Established research company needs fresh new powerpoint template

We need a powerpoint template for an established research and advisory company called Quenlow Partnership. We develop policy, improve delivery, and build capacity within the public sector - mainly in relation to education and young people.

We have a long and successful track record in our sector, and have a grown-up, clean brand. We already have a logo (see attached) and want a simple, clean powerpoint template that incorporates our logo and colours and matches the brand identity on our website: https://www.quenlowpartnership.com/

We need a title slide, a section header slide, a two-column slide for two panels of text, a two-column slide for one panel of text and one panel of imagery, and a single-column slide for text.

We want a template with built-in Styles so our team can make consistent-looking presentations without any manual formatting. We also want to use a font that will be compatible with devices used across a range of clients.

```html
<!DOCTYPE html>
<html lang="en">
<head>
<meta charset="utf-8">
<title>Quenlow Partnership – Presentation Template</title>
<link href="https://fonts.googleapis.com/css2?family=Poppins:wght@400;500;600;700&family=Roboto:wght@400;500;700&display=swap" rel="stylesheet">
<style>
  :root{
    --orange:#f07a31;
    --ink:#262626;
    --body:#5b5b5b;
    --grey:#8d929d;
    --number:#dcdcdc;
    --page:#ffffff;
    --dark:#2a2b2f;
    --navy:#141b36;
  }
  *{box-sizing:border-box;margin:0;padding:0}
  html,body{width:1200px;height:4110px;overflow:hidden;background:var(--page)}
  body{position:relative;font-family:"Poppins",sans-serif;color:var(--body)}
  .slide{position:absolute;left:66px;width:1072px;height:602px;background:#fff;box-shadow:0 2px 14px rgba(0,0,0,.08);overflow:hidden}
  .s1{top:64px;background:var(--dark)}
  .s2{top:741px}.s3{top:1413px}.s4{top:2082px}.s5{top:2752px}
  .s6{top:3456px;background:var(--navy)}
  .slide-title{position:absolute;left:90px;top:78px;font-weight:700;font-size:49px;color:var(--ink);line-height:1.1;white-space:nowrap}
  .slide-title::after{content:"";position:absolute;left:0;top:74px;width:72px;height:4px;background:var(--orange)}
  .footer{position:absolute;left:0;right:90px;top:530px;height:43px;display:flex;justify-content:flex-end;align-items:center;gap:26px}
  .copyright{font-family:"Roboto",sans-serif;font-size:13px;color:#555}
  .page-no{width:42px;height:43px;background:var(--orange);color:#fff;font-family:"Roboto",sans-serif;font-weight:500;font-size:16px;display:flex;align-items:center;justify-content:center;border-radius:2px}
  .copy{font-size:12.2px;line-height:27px;text-align:justify;color:var(--body)}
  .copy p+p{margin-top:27px}

  /* title slide */
  .hero-photo{position:absolute;inset:0;background:radial-gradient(circle at 65% 40%,#3a3b40 0%,#2a2b2f 45%,#1f2023 100%)}
  .brand-card{position:absolute;left:0;top:181px;width:536px;height:230px;background:#fff}
  .brand-name{position:absolute;left:88px;top:40px;font-weight:600;font-size:56px;line-height:62px;color:var(--grey)}
  .brand-bar{position:absolute;left:0;top:400px;width:450px;height:18px;background:var(--orange)}
  .dot{position:absolute;border-radius:50%;background:#a7abb4}
  .side-bar{position:absolute;left:1036px;top:480px;width:36px;height:122px;background:var(--orange)}

  /* contents */
  .toc{position:absolute;left:90px;top:200px;width:900px;display:grid;grid-template-columns:457px 443px;row-gap:38px}
  .toc-item{display:flex;align-items:center;height:71px}
  .toc-num{width:42px;font-family:"Roboto",sans-serif;font-weight:700;font-size:66px;color:var(--number);line-height:1;text-align:center}
  .toc-rule{width:2px;height:56px;background:#e6e6e6;margin:0 20px 0 4px}
  .toc-head{font-family:"Roboto",sans-serif;font-weight:500;font-size:25px;color:var(--orange);line-height:1.2}
  .toc-sub{font-family:"Roboto",sans-serif;font-size:11px;color:#666;margin-top:8px}

  /* who we are */
  .s3 .copy{position:absolute;left:90px;top:196px;width:426px}
  .team-photo{position:absolute;left:565px;top:94px;width:418px;height:400px;border-radius:34px 0 34px 0;background:linear-gradient(160deg,#55636b 0%,#2b3a4a 45%,#1c2635 75%,#8a6a4a 100%)}

  /* strategic planning */
  .col{position:absolute;top:180px;width:426px}
  .col.left{left:90px}.col.right{left:556px}

  /* publications */
  .pub-head{position:absolute;left:90px;top:196px;width:893px;font-weight:700;font-size:14.5px;line-height:27px;color:var(--orange);text-transform:uppercase;text-align:justify}
  .s5 .copy{position:absolute;left:90px;top:275px;width:893px;font-size:12px}

  /* thank you */
  .handover-photo{position:absolute;left:560px;top:0;width:512px;height:602px;background:linear-gradient(100deg,rgba(20,27,54,1) 0%,rgba(31,40,70,.9) 35%,#2d3558 55%,#6b5038 80%,#4a3424 100%)}
  .s6 .slide-title{color:#fff}
  .contact{position:absolute;left:88px;display:flex;align-items:center;gap:26px;font-size:18px;color:#fff}
  .contact .icon{width:56px;height:56px;border-radius:50%;background:var(--orange);display:flex;align-items:center;justify-content:center}
</style>
</head>
<body>

<section class="slide s1">
  <div class="hero-photo" role="img" aria-label="Overhead photo of business people meeting around a table"></div>
  <div class="brand-card">
    <div class="brand-name">Quenlow<br>Partnership</div>
  </div>
  <div class="brand-bar"></div>
  <div class="dot" style="left:467px;top:399px;width:22px;height:22px"></div>
  <div class="dot" style="left:1032px;top:413px;width:38px;height:38px"></div>
  <div class="side-bar"></div>
</section>

<section class="slide s2">
  <h1 class="slide-title">Table of contents</h1>
  <div class="toc">
    <div class="toc-item"><span class="toc-num">1</span><span class="toc-rule"></span><div><div class="toc-head">Introduction</div><div class="toc-sub">We help the public sector solve problems and deliver effectively</div></div></div>
    <div class="toc-item"><span class="toc-num">4</span><span class="toc-rule"></span><div><div class="toc-head">Strategic Planning</div><div class="toc-sub">The projects on which we are working currently</div></div></div>
    <div class="toc-item"><span class="toc-num">2</span><span class="toc-rule"></span><div><div class="toc-head">Agenda</div><div class="toc-sub">We help the public sector solve problems and deliver effectively</div></div></div>
    <div class="toc-item"><span class="toc-num">5</span><span class="toc-rule"></span><div><div class="toc-head">Our Publications</div><div class="toc-sub">Research and advisory company with a track-record</div></div></div>
    <div class="toc-item"><span class="toc-num">3</span><span class="toc-rule"></span><div><div class="toc-head">Who we are</div><div class="toc-sub">Find out how we can help you to deliver more effectively</div></div></div>
    <div class="toc-item"><span class="toc-num">6</span><span class="toc-rule"></span><div><div class="toc-head">Thank You</div><div class="toc-sub">Joining our team and working with Quenlow Partnership</div></div></div>
  </div>
  <div class="footer"><span class="copyright">(C) Copyright 2023 | All Rights Reserved</span><span class="page-no">02</span></div>
</section>

<section class="slide s3">
  <h1 class="slide-title">Who We Are</h1>
  <div class="copy">
    <p>We have in-depth experience of working with the public sector, in the UK and overseas, in education, local government, health and social care. We have expertise and a proven track record in developing policy and strategy, solving delivery problems, undertaking national evaluations and writing influential research reports, advising on organisational reform, and facilitating workshops and conferences.</p>
    <p>On many of our projects, we work with our expert research partners. They have an array of experience in carrying out research and delivering improvements in public services, and they bring a wide range of skills and expertise to our work.</p>
  </div>
  <div class="team-photo" role="img" aria-label="Photo of two colleagues in business suits walking through an office"></div>
  <div class="footer"><span class="copyright">(C) Copyright 2023 | All Rights Reserved</span><span class="page-no">03</span></div>
</section>

<section class="slide s4">
  <h1 class="slide-title">Strategic Planning</h1>
  <div class="col left copy"><p>Many local areas are experiencing considerable pressure in relation to support for young people with special educational needs. We have undertaken major pieces of national research that have helped to shape the evidence base at a national level about the extent of and factors driving these pressures, at a national level and specifically within the capital, as well the actions that local areas can take to mitigate these challenges and embed effective practice at local level. We have worked and are currently working with local areas to develop new, partnership-based strategic approaches to using local resource to support young people with special educational needs, including Ashby Vale, Brenmouth, Calderfield, the East Riding of Hollinshire,</p></div>
  <div class="col right copy"><p>West Marsden, Fenwick, Lornley, North Dalbury, Redbrook, Stanholt and Wexcombe.</p><p>We recently undertook a significant piece of national research, commissioned by the Northmere Education Office, that sought to understand how local areas arranged alternative provision and what we the characteristics of an effective local inclusion support and alternative provision system. We have been invited to present the findings of this work at national conferences, and we are using the findings from this research to support leaders in local areas to consider and develop effective inclusion support and AP arrangements within their local systems</p></div>
  <div class="footer"><span class="copyright">(C) Copyright 2023 | All Rights Reserved</span><span class="page-no">04</span></div>
</section>

<section class="slide s5">
  <h1 class="slide-title">Our Publications</h1>
  <h2 class="pub-head">Preliminary research into how trusts and schools narrow attainment gaps between pupils from different ethnic groups</h2>
  <div class="copy">
    <p>In January 2023, the Northmere Education Office, working with the Civic Fairness Unit, commissioned Quenlow Partnership to undertake exploratory research into how academy trusts and schools have improved the achievement of, and closed achievement gaps between, pupils from different ethnic groups. The research took place during the spring term and the first half of the summer term 2023, and involved discussions with trust and school leaders within nine academy trusts, one maintained school and national education sector organisations.</p>
    <p>The research was designed to be exploratory. It focused on the role and practices of trusts and schools. The evidence we gathered came from interviews with the leaders of nine academy trusts and leaders of individual schools within those trusts (plus one local authority maintained school). It was not within the scope of the research to gather evidence on the extent of ethnic disparities or discrimination that may be experienced by pupils and staff. These are important areas of study in their own right.</p>
  </div>
  <div class="footer"><span class="copyright">(C) Copyright 2023 | All Rights Reserved</span><span class="page-no">05</span></div>
</section>

<section class="slide s6">
  <div class="handover-photo" role="img" aria-label="Photo of a hand passing an envelope across a wooden desk"></div>
  <h1 class="slide-title">Thank You</h1>
  <div class="contact" style="top:330px">
    <span class="icon"><svg width="22" height="16" viewBox="0 0 22 16"><rect x="1" y="1" width="20" height="14" rx="1.5" fill="none" stroke="#fff" stroke-width="2"/><path d="M1.5 2l9.5 7 9.5-7" fill="none" stroke="#fff" stroke-width="2"/></svg></span>
    <span>info@quenlowpartnership.com</span>
  </div>
  <div class="contact" style="top:422px">
    <span class="icon"><svg width="22" height="22" viewBox="0 0 22 22" fill="none" stroke="#fff" stroke-width="1.8"><circle cx="11" cy="11" r="9"/><ellipse cx="11" cy="11" rx="4" ry="9"/><path d="M2 11h18M4 6h14M4 16h14"/></svg></span>
    <span>www.quenlowpartnership.com</span>
  </div>
</section>

</body>
</html>
```